website update

We need to redesign our current website to be more personalised and sophisticated. We are physiotherapy clinic based in sydney australia, offer a range of clinical service such as Physiotherapy, Massage, sports injuries rehabilitation, Women's health (incontinency etc), Pilates classes, back pain exercise program, acupuncture, Gait analysis.
our current website is www.brightlanehealth.com.au
an example of ideal website is http://quillbrookrehabstudio.com/
homepage: with a revolving displaying attached photos which is linked to relevants page

```html
<!DOCTYPE html>
<html lang="en">
<head>
<meta charset="utf-8">
<title>Brightlane Physiotherapy &amp; Sports Clinic</title>
<link rel="stylesheet" href="https://fonts.googleapis.com/css2?family=Open+Sans:wght@400;600;700&display=swap">
<style>
:root{
  --green:#2f9c50;
  --green-text:#2a9a4a;
  --lime:#d4e86a;
  --ink:#333;
  --muted:#666;
  --line:#e2e2e2;
  --topbar:#eeeeef;
  --page:#f4f4f4;
  --footer:#3a3a3a;
  --footer-text:#ececec;
}
*{margin:0;padding:0;box-sizing:border-box}
html,body{width:752px;height:1200px;overflow:hidden}
body{position:relative;background:var(--page);font-family:"Open Sans",Arial,sans-serif;color:var(--ink)}
.abs{position:absolute}
.topbar{left:0;top:0;width:752px;height:31px;background:var(--topbar)}
.connect{left:563px;top:11px;font-size:7px;color:var(--muted)}
.social{left:598px;top:10px;display:flex;gap:6px}
.social span{width:12px;height:12px;border-radius:50%;background:#b9b9b9}
.header{left:0;top:31px;width:752px;height:66px;background:#fff}
.brand{left:82px;top:44px;display:flex;align-items:center;gap:7px}
.brand-dot{width:30px;height:30px;border-radius:50%;background:var(--green)}
.brand-name{font-size:17px;font-weight:600;color:var(--green-text);letter-spacing:-.3px}
.appoint{right:82px;top:48px;font-size:8px;color:var(--ink);display:flex;align-items:center;gap:8px}
.phones{right:82px;top:67px;font-size:8px;color:var(--ink)}
.phones b{font-weight:400;color:var(--green-text)}
.nav{left:0;top:97px;width:752px;height:29px;background:var(--green)}
.nav a{position:absolute;top:9px;font-size:8.5px;color:#fff;text-decoration:none}
.nav a.current{color:var(--lime)}
.slider{left:82px;top:143px;width:588px;height:275px;background:linear-gradient(135deg,#e4e4e4 0%,#cfcfcf 45%,#b0a0a8 70%,#5a5a5e 100%)}
.slide-arrow{top:266px;width:22px;height:22px}
.intro{left:0;top:457px;width:752px;text-align:center;font-size:10px;color:var(--ink);line-height:22px}
.intro strong{font-size:16px;font-weight:700;color:var(--green-text)}
.service{top:513px;width:138px;text-align:center}
.service-img{width:138px;height:90px}
.service h3{margin-top:14px;font-size:13px;font-weight:600;color:#222}
.service p{margin-top:6px;font-size:7.5px;line-height:13px;color:var(--muted)}
.next{left:682px;top:553px;width:18px;height:18px}
.rule{left:82px;width:588px;height:1px;background:var(--line)}
.welcome{left:83px;top:711px;font-size:14px;font-weight:400;color:#222}
.welcome span{color:var(--green-text)}
.col h4{font-size:11px;font-weight:400;color:var(--green-text)}
.col h5{font-size:10px;font-weight:400;color:var(--green-text)}
.col ul{list-style:none}
.col li{font-size:7.5px;line-height:15.7px;color:#444;padding-left:12px;position:relative}
.col li::before{content:"";position:absolute;left:2px;top:6.5px;width:3px;height:3px;border-radius:50%;background:var(--green)}
.col .more{display:block;font-size:7.5px;line-height:15.7px;color:var(--green-text);padding-left:12px}
.partner{top:1018px;width:88px;height:56px;background:#fff;display:flex;align-items:center;justify-content:center}
.partner span{width:60px;height:20px;border-radius:3px}
.footer{left:0;top:1108px;width:752px;height:92px;background:var(--footer);color:var(--footer-text);font-size:7.5px}
.footer .mail{left:83px;top:24px}
.footer .mail b{font-weight:400;color:var(--lime)}
.footer .addr{left:83px;top:44px;line-height:16px}
.to-top{left:637px;top:34px;width:32px;height:32px;background:#222;border-radius:2px;color:#fff;font-size:8px;text-align:center;padding-top:15px}
</style>
</head>
<body>

<div class="abs topbar"></div>
<div class="abs connect">Connect</div>
<div class="abs social"><span></span><span></span><span></span><span></span></div>

<div class="abs header"></div>
<div class="abs brand"><span class="brand-dot"></span><span class="brand-name">brightlane</span></div>
<div class="abs appoint">
  <svg width="12" height="12" viewBox="0 0 24 24" fill="none" stroke="#333" stroke-width="2"><path d="M5 3h4l2 5-3 2a12 12 0 0 0 6 6l2-3 5 2v4a2 2 0 0 1-2 2A17 17 0 0 1 3 5a2 2 0 0 1 2-2z"/></svg>
  Make An Appointments
</div>
<div class="abs phones">Ryde: <b>02 5550 1842</b>, &nbsp; Chatswood : <b>02 5550 3961</b></div>

<nav class="abs nav">
  <a class="current" style="left:94px">Home</a>
  <a style="left:138px">About us</a>
  <a style="left:187px">Common conditions</a>
  <a style="left:282px">Treatments</a>
  <a style="left:341px">Specialised services</a>
  <a style="left:431px">OH&amp;S / Workplace Assessment</a>
  <a style="left:566px">Contact Us</a>
</nav>

<div class="abs slider" role="img" aria-label="Physiotherapist guiding a woman through a stretch on a Pilates reformer"></div>
<svg class="abs slide-arrow" style="left:93px" viewBox="0 0 22 22"><circle cx="11" cy="11" r="10" fill="none" stroke="#fff" stroke-width="1.5" opacity=".8"/><path d="M13 6l-5 5 5 5" fill="none" stroke="#fff" stroke-width="1.5" opacity=".8"/></svg>
<svg class="abs slide-arrow" style="left:633px" viewBox="0 0 22 22"><circle cx="11" cy="11" r="10" fill="none" stroke="#fff" stroke-width="1.5" opacity=".8"/><path d="M9 6l5 5-5 5" fill="none" stroke="#fff" stroke-width="1.5" opacity=".8"/></svg>

<div class="abs intro">We are physiotherapy clinic based in sydney australia, offer<br>a range of <strong>Clinical Service</strong> such as</div>

<div class="abs service" style="left:82px"><div class="service-img" role="img" aria-label="Runner on a treadmill during gait analysis" style="background:linear-gradient(135deg,#d8d8d8,#8a8a8a)"></div><h3>Gait Analysis</h3><p>Neque porro quisquam est qui<br>dolorem ipsum dolor</p></div>
<div class="abs service" style="left:231px"><div class="service-img" role="img" aria-label="Acupuncture needles being placed" style="background:linear-gradient(135deg,#e6c7b0,#3b3b3b)"></div><h3>Acupuncture</h3><p>Neque porro quisquam est qui<br>dolorem ipsum dolor</p></div>
<div class="abs service" style="left:382px"><div class="service-img" role="img" aria-label="Spine model used in Pilates classes" style="background:linear-gradient(135deg,#c8c8c8,#d8b07a)"></div><h3>Pilates classes</h3><p>Neque porro quisquam est qui<br>dolorem ipsum dolor</p></div>
<div class="abs service" style="left:531px"><div class="service-img" role="img" aria-label="Clinician examining a patient lying down" style="background:linear-gradient(135deg,#e8e8e8,#5a5a5a)"></div><h3>Examine</h3><p>Neque porro quisquam est qui<br>dolorem ipsum dolor</p></div>
<svg class="abs next" viewBox="0 0 18 18"><circle cx="9" cy="9" r="8" fill="none" stroke="#ddd" stroke-width="1.2"/><path d="M7.5 5.5l3.5 3.5-3.5 3.5" fill="none" stroke="#ddd" stroke-width="1.2"/></svg>

<div class="abs rule" style="top:682px"></div>

<h2 class="abs welcome">Welcome to <span>Brightlane Spinal &amp; Sports physiotherapy clinic</span></h2>

<div class="abs col" style="left:83px;top:744px">
  <h4>We treat</h4>
  <ul style="margin-top:6px">
    <li>Back and low back pain</li><li>Neck pain and Headaches</li><li>Spinal/ Posture disorders</li><li>Sport injuries</li><li>Work Injuries/ Motor vehicle accident</li><li>Knee/shoulder pain</li><li>Arthritis</li>
  </ul>
  <span class="more">more details...</span>
</div>

<div class="abs col" style="left:283px;top:746px">
  <h4>We offer</h4>
  <ul style="margin-top:10px">
    <li>Manual therapy and spinal manipulation</li><li>Acupuncture/Dry Needling</li><li>Electrical Therapy</li><li>Spinal strengthening (core stability training<br>with real-time ultrasound device)</li><li>Sports Injuries rehabilitation</li><li>Post Operative rehabilitation</li><li>Custom-made orthotics</li>
  </ul>
  <span class="more">more details...</span>
</div>

<div class="abs col" style="left:485px;top:747px">
  <h4>Specialised services include</h4>
  <h5 style="margin-top:9px;padding-left:2px">Inhouse</h5>
  <ul style="margin-top:1px">
    <li>Runner's assessment and training</li><li>Computer Spinal/Posture Assessment</li><li>Computer gait/running analysis</li><li>Computer foot assessment</li><li>Real time Ultrasound Assessment and<br>Training</li>
  </ul>
  <h5 style="margin-top:10px;padding-left:2px">Onsite visit</h5>
  <ul>
    <li>OH&amp;S Assessment</li><li>Office workplace Assessment</li>
  </ul>
  <span class="more" style="padding-left:2px">more details...</span>
</div>

<div class="abs rule" style="top:986px"></div>

<div class="abs partner" style="left:82px"><span style="background:#1f6fb7"></span></div>
<div class="abs partner" style="left:182px"><span style="background:#c8343a"></span></div>
<div class="abs partner" style="left:282px"><span style="background:#1a8ad0;width:40px"></span></div>
<div class="abs partner" style="left:381px"><span style="background:#1c8a4c;width:34px"></span></div>
<div class="abs partner" style="left:482px"><span style="background:#e0312f;width:68px;height:14px"></span></div>
<div class="abs partner" style="left:582px"><span style="background:#34a04a;width:66px;height:16px"></span></div>

<footer class="abs footer">
  <div class="abs mail">Email: <b>info@brightlanehealth.com.au</b></div>
  <div class="abs addr">Shop 8, The Arcade, 212 Fernleigh Ave, Chatswood 2067 &nbsp;[See a map]<br>Shop 2, 18-20 Wattle Rd Ryde 2112 Australia &nbsp;[See a map]</div>
  <div class="abs to-top">TOP</div>
</footer>

</body>
</html>
```